Need Flyer for Our Real estate Agency

Need to run General Campaign for our agency with Start of New Year as our theme ..Must have an agent's picture on the DL..
Address:
27 / 486Brindle rd, Marsden VIC 3047
Ph:03 9412 7306
email:info@kovalinrealestate.com.au
www.kovalinrealestate.com.au
Something like as attached picture..
Target Market(s)
Home Buyers
Industry/Entity Type
Real Estate Agent
Requirements
Must have
- Our Logo Colours

```html
<!DOCTYPE html>
<html lang="en">
<head>
<meta charset="utf-8">
<title>Kovalin Real Estate – New Year DL Flyer</title>
<link rel="stylesheet" href="https://fonts.googleapis.com/css2?family=Lato:wght@400;700&display=swap">
<style>
  :root {
    --navy: #0f2461;
    --navy-deep: #0a1a4a;
    --navy-light: #1c3a82;
    --maroon: #7a1420;
    --silver: #d4d6da;
    --white: #ffffff;
    --page: #e9e7e4;
    --body-font: "Lato", "Helvetica Neue", Arial, sans-serif;
  }
  * { box-sizing: border-box; margin: 0; padding: 0; }
  html, body { width: 1192px; height: 1200px; overflow: hidden; background: var(--page); }
  body { position: relative; font-family: var(--body-font); color: var(--white); }

  .card {
    position: absolute; left: 102px; width: 988px; height: 470px;
    overflow: hidden; box-shadow: 0 6px 18px rgba(0,0,0,.25);
  }
  .card--front { top: 80px; }
  .card--back { top: 640px; }
  .card__art { position: absolute; inset: 0; width: 100%; height: 100%; display: block; }

  .brand {
    position: absolute; transform: translateX(-50%);
    display: flex; align-items: center; gap: 12px;
    font-family: var(--body-font); font-weight: 400;
    font-size: 50px; letter-spacing: 6px; color: var(--white); white-space: nowrap;
  }
  .brand__mark { width: 14px; height: 14px; background: var(--white); }

  .headline {
    position: absolute; left: 0; width: 540px; text-align: center;
    font-weight: 400; font-size: 31px; line-height: 45px;
  }
  .subline {
    position: absolute; left: 0; width: 540px; text-align: center;
    font-size: 16px; letter-spacing: .2px;
  }
  .subline strong { font-weight: 700; }

  .cta {
    position: absolute; left: 86px; top: 380px; width: 368px; height: 46px;
    background: var(--white); border-radius: 23px;
    box-shadow: 0 3px 6px rgba(0,0,0,.3);
    display: flex; align-items: center; justify-content: center; gap: 8px;
    color: var(--maroon); font-weight: 700; font-size: 22px; letter-spacing: .2px;
  }
  .cta svg { width: 22px; height: 22px; }
  .cta__note {
    position: absolute; left: 0; width: 540px; top: 432px; text-align: center;
    font-size: 18px;
  }

  .contact { position: absolute; left: 563px; }
  .contact__name { top: 222px; font-size: 22px; }
  .contact__line {
    display: flex; align-items: center; gap: 12px; font-size: 19px;
  }
  .contact__line svg { width: 19px; height: 19px; flex: none; }
  .contact__phone { top: 270px; }
  .contact__email { top: 306px; }
  .contact__web { top: 342px; }
  .address {
    position: absolute; left: 440px; width: 548px; top: 421px; text-align: center;
    font-size: 18.5px; letter-spacing: .3px;
  }
</style>
</head>
<body>

<!-- Front of DL flyer -->
<section class="card card--front">
  <svg class="card__art" viewBox="0 0 988 470" preserveAspectRatio="none">
    <defs>
      <linearGradient id="front-navy" x1="0" y1="0" x2="1" y2="0">
        <stop offset="0" stop-color="#0b1c50"/>
        <stop offset=".6" stop-color="#13296b"/>
        <stop offset="1" stop-color="#0d2259"/>
      </linearGradient>
      <linearGradient id="front-photo" x1="0" y1="0" x2="0" y2="1">
        <stop offset="0" stop-color="#b9c9dc"/>
        <stop offset=".45" stop-color="#a49c94"/>
        <stop offset=".75" stop-color="#2f4c8f"/>
        <stop offset="1" stop-color="#4c7a3a"/>
      </linearGradient>
    </defs>
    <rect width="988" height="470" fill="url(#front-navy)"/>
    <path d="M0 470 L180 290 L230 290 L50 470 Z M60 0 L0 60 L0 20 L20 0 Z" fill="#ffffff" opacity=".03"/>
    <rect x="0" y="402" width="988" height="68" fill="var(--maroon)"/>
    <rect x="0" y="399" width="988" height="3" fill="var(--white)"/>
    <path d="M668 0 L700 0 C628 120 600 320 620 470 L588 470 C568 320 596 120 668 0 Z" fill="var(--silver)"/>
    <path d="M700 0 L988 0 L988 470 L620 470 C600 320 628 120 700 0 Z" fill="#ffffff"/>
    <g role="img" aria-label="Photo of the agent in a blue suit standing in front of a large two-storey family home">
      <path d="M706 0 L988 0 L988 470 L626 470 C606 320 634 120 706 0 Z" fill="url(#front-photo)"/>
    </g>
  </svg>

  <div class="brand" style="left:271px; top:112px;"><span class="brand__mark"></span>KOVALIN</div>
  <p class="headline" style="top:218px;">Curios to know what your<br>home is worth?</p>
  <p class="subline" style="top:330px;">START OF NEW YEAR WITH <strong>DANIEL MERCER</strong> AND FIND OUT!</p>
  <div class="cta">
    CALL ME NOW!
    <svg viewBox="0 0 24 24" aria-hidden="true"><circle cx="12" cy="12" r="10.5" fill="none" stroke="currentColor" stroke-width="2"/><path d="M8.2 6.8c.5-.4 1.1-.3 1.4.2l1 1.7c.3.5.1 1-.3 1.3l-.6.4c.5 1.4 1.5 2.5 2.9 3.1l.4-.6c.3-.4.9-.6 1.3-.3l1.7 1c.5.3.6 1 .2 1.4l-.8.8c-.7.7-2 .8-3.2.2-2.3-1.1-4-2.9-5-5.2-.5-1.2-.4-2.4.3-3.1z" fill="currentColor"/></svg>
    03 9412 7306
  </div>
  <p class="cta__note">For Free property Appraisal</p>
</section>

<!-- Back of DL flyer -->
<section class="card card--back">
  <svg class="card__art" viewBox="0 0 988 470" preserveAspectRatio="none">
    <defs>
      <linearGradient id="back-navy" x1="0" y1="0" x2="1" y2="0">
        <stop offset="0" stop-color="#13296b"/>
        <stop offset="1" stop-color="#0b1c50"/>
      </linearGradient>
      <linearGradient id="back-photo" x1="0" y1="0" x2="1" y2="1">
        <stop offset="0" stop-color="#c79a84"/>
        <stop offset=".45" stop-color="#d6d3cf"/>
        <stop offset=".6" stop-color="#d9534f"/>
        <stop offset="1" stop-color="#1d2a44"/>
      </linearGradient>
    </defs>
    <rect width="988" height="470" fill="url(#back-navy)"/>
    <path d="M988 120 L860 248 L860 298 L988 170 Z" fill="#ffffff" opacity=".03"/>
    <rect x="0" y="405" width="988" height="65" fill="var(--maroon)"/>
    <rect x="0" y="402" width="988" height="3" fill="var(--white)"/>
    <path d="M395 0 L425 0 C370 150 366 330 430 470 L400 470 C336 330 340 150 395 0 Z" fill="var(--silver)"/>
    <path d="M0 0 L395 0 C340 150 336 330 400 470 L0 470 Z" fill="#ffffff"/>
    <g role="img" aria-label="Photo of two hands sheltering a small red model house">
      <path d="M0 0 L389 0 C334 150 330 330 394 470 L0 470 Z" fill="url(#back-photo)"/>
    </g>
  </svg>

  <div class="brand" style="left:714px; top:112px;"><span class="brand__mark"></span>KOVALIN</div>
  <p class="contact contact__name">Daniel Mercer, Director</p>
  <p class="contact contact__line contact__phone">
    <svg viewBox="0 0 24 24" aria-hidden="true"><circle cx="12" cy="12" r="10.5" fill="none" stroke="#fff" stroke-width="2"/><path d="M8.2 6.8c.5-.4 1.1-.3 1.4.2l1 1.7c.3.5.1 1-.3 1.3l-.6.4c.5 1.4 1.5 2.5 2.9 3.1l.4-.6c.3-.4.9-.6 1.3-.3l1.7 1c.5.3.6 1 .2 1.4l-.8.8c-.7.7-2 .8-3.2.2-2.3-1.1-4-2.9-5-5.2-.5-1.2-.4-2.4.3-3.1z" fill="#fff"/></svg>
    0433 582 914
  </p>
  <p class="contact contact__line contact__email">
    <svg viewBox="0 0 24 24" aria-hidden="true"><circle cx="12" cy="12" r="10.5" fill="none" stroke="#fff" stroke-width="2"/><rect x="6.5" y="8" width="11" height="8" fill="#fff"/><path d="M6.5 8 L12 12.5 L17.5 8" fill="none" stroke="#13296b" stroke-width="1.3"/></svg>
    daniel.mercer@kovalinrealestate.com.au
  </p>
  <p class="contact contact__line contact__web">
    <svg viewBox="0 0 24 24" aria-hidden="true" fill="none" stroke="#fff" stroke-width="1.6"><circle cx="12" cy="12" r="10.5" stroke-width="2"/><circle cx="12" cy="12" r="6"/><ellipse cx="12" cy="12" rx="2.6" ry="6"/><path d="M6 12h12"/></svg>
    www.kovalinrealestate.com.au
  </p>
  <p class="address">27/486 Brindle Rd Marsden, Victoria, Australia 3047</p>
</section>

</body>
</html>
```